TA BRAMLEY BUSINESS CARD DESIGN PROJECT

We need to utilize our logo that was expertly created on PixelHarbor and now need to match this with a business card design.

```html
<!DOCTYPE html>
<html lang="en">
<head>
<meta charset="utf-8">
<title>TA Bramley Business Card</title>
<link href="https://fonts.googleapis.com/css2?family=Montserrat:wght@400;500;700&display=swap" rel="stylesheet">
<style>
  :root {
    --backdrop: #2e2e2e;
    --card-black: #161616;
    --card-dark: #1b1b1b;
    --emboss: #2c2c2c;
    --brand-blue: #1357b0;
    --paper: #ffffff;
    --ink-light: #f2f2f2;
  }
  * { margin: 0; padding: 0; box-sizing: border-box; }
  html, body { width: 1200px; height: 689px; overflow: hidden; }
  body {
    background: var(--backdrop);
    font-family: "Montserrat", sans-serif;
    position: relative;
  }
  .card {
    position: absolute;
    top: 190px;
    width: 540px;
    height: 310px;
    border-radius: 18px;
    overflow: hidden;
    box-shadow: 0 18px 40px rgba(0,0,0,0.45);
  }
  .card-back { left: 40px; background: var(--card-black); }
  .card-front { left: 620px; background: var(--paper); }

  .back-brand {
    position: absolute;
    inset: 0;
    display: flex;
    align-items: center;
    justify-content: center;
    gap: 18px;
  }
  .back-brand .brand-dot {
    width: 34px; height: 34px; border-radius: 50%;
    background: var(--emboss);
  }
  .back-brand .brand-name {
    font-weight: 700;
    font-size: 46px;
    letter-spacing: 6px;
    color: var(--emboss);
  }

  .front-shape { position: absolute; inset: 0; }

  .front-brand {
    position: absolute;
    left: 30px;
    top: 112px;
    display: flex;
    align-items: center;
    gap: 8px;
  }
  .front-brand .brand-dot {
    width: 18px; height: 18px; border-radius: 50%;
    background: var(--brand-blue);
  }
  .front-brand .brand-name {
    font-weight: 700;
    font-size: 22px;
    letter-spacing: 2px;
    color: var(--brand-blue);
  }

  .accent-bar {
    position: absolute;
    right: 0;
    top: 58px;
    width: 8px;
    height: 34px;
    background: var(--brand-blue);
  }
  .contact {
    position: absolute;
    right: 24px;
    top: 60px;
    text-align: right;
    color: var(--ink-light);
  }
  .contact .person-name {
    font-weight: 700;
    font-size: 17px;
    color: var(--brand-blue);
    letter-spacing: 0.5px;
  }
  .contact .person-role {
    font-size: 11px;
    margin-bottom: 12px;
  }
  .contact-line {
    font-size: 11px;
    line-height: 17px;
    display: flex;
    justify-content: flex-end;
    align-items: center;
    gap: 6px;
  }
  .contact-line svg { width: 10px; height: 10px; fill: var(--brand-blue); }
  .contact .address {
    font-size: 11px;
    line-height: 16px;
    margin-top: 10px;
    padding-right: 16px;
  }
</style>
</head>
<body>

  <section class="card card-back">
    <div class="back-brand">
      <span class="brand-dot"></span>
      <span class="brand-name">TA BRAMLEY</span>
    </div>
  </section>

  <section class="card card-front">
    <svg class="front-shape" viewBox="0 0 540 310" width="540" height="310">
      <path d="M392 0 C290 40 300 210 96 310 L540 310 L540 0 Z" fill="var(--brand-blue)"/>
      <path d="M412 0 C312 46 318 214 122 310 L540 310 L540 0 Z" fill="var(--paper)"/>
      <path d="M418 0 C318 48 324 216 130 310 L540 310 L540 0 Z" fill="var(--card-dark)"/>
    </svg>

    <div class="front-brand">
      <span class="brand-dot"></span>
      <span class="brand-name">TA BRAMLEY</span>
    </div>

    <span class="accent-bar"></span>

    <div class="contact">
      <div class="person-name">COLIN MARSH</div>
      <div class="person-role">Managing Director</div>
      <div class="contact-line">123 456 789
        <svg viewBox="0 0 10 10"><path d="M2 0.5 L4 2.5 L3 3.8 Q4.5 6 6.2 7 L7.5 6 L9.5 8 L8 9.5 Q3 9 0.5 2 Z"/></svg>
      </div>
      <div class="contact-line">123 456 789
        <svg viewBox="0 0 10 10"><rect x="1" y="3" width="8" height="6" rx="1"/><rect x="3" y="0.5" width="4" height="3"/></svg>
      </div>
      <div class="contact-line">info@yourmail.com
        <svg viewBox="0 0 10 10"><path d="M0.5 2 H9.5 V8.5 H0.5 Z M0.5 2 L5 5.5 L9.5 2" stroke="#1b1b1b" stroke-width="0.6"/></svg>
      </div>
      <div class="contact-line">www.yourwebsite.com
        <svg viewBox="0 0 10 10"><circle cx="5" cy="5" r="4.5"/></svg>
      </div>
      <div class="address">Your address, City<br>State, Zip 1234</div>
    </div>
  </section>

</body>
</html>
```